Fernhill Shopping Centre main sign re-design project

We would like to refresh the look of the main sign we have on the corner of a block of shops to make it more contemproary and vibrant.

A picture of the existing sign which reads Fernhill Shopping Centre can be found in attached PDF and at the following URL.

http://www.quorvelprop.co.nz/~/media/Listings/Region%20Sample/Sample%20City/Sample%20CBD/418206/Images/418206_1.ashx?bc=Gainsboro&as=1&h=550&w=980&ma=1

Fernhill Shopping Centre is also know locally as Fernhill Plaza, but the key word is Fernhill.

The existing signage has a flower/clover pattern on it which I think was just added to create a bit of interest. The building is located in a town surrounded by farm land.

I do quite like the organic feel of plant leaves or certain flowers - preferably New Zealand native plants for instance - the Kowhai flower or leaf block, pohutukawa, or kaka beak - reference images can be found with google image search

Geometric patterns could also be an option.

Once again the imagery is only to soften the sign and add some interest.

Target Market(s)

The target audience is premium shopper

Industry/Entity Type

Building

Requirements
Must have
• Must have the words: Fernhill Shopping Centre.
The big M is not essential, and I would rather the emphasis was on the word Fernhill.
Should not have
• Should not be brown. We want the sign to feel more contemporary, but not too hard. The current pale brown feels too soft in comparison with the look of the building.

```html
<!DOCTYPE html>
<html lang="en">
<head>
<meta charset="utf-8">
<title>Fernhill Shopping Centre – Main Sign</title>
<link rel="stylesheet" href="https://fonts.googleapis.com/css2?family=Poppins:wght@700&family=Patrick+Hand&display=swap">
<style>
  :root {
    --frame-violet: #4b2a7e;
    --sky-blue: #2f98dc;
    --sky-blue-light: #4cb2ec;
    --band-pale: #cfeaf8;
    --band-white: #f4fbff;
    --leaf-green: #3f8d3b;
    --leaf-green-light: #5aa84e;
    --lettering-white: #ffffff;
  }
  html, body {
    margin: 0;
    padding: 0;
    overflow: hidden;
    background: #ffffff;
  }
  .sign {
    position: relative;
    width: 730px;
    height: 1200px;
    box-sizing: border-box;
    border: 24px solid var(--frame-violet);
    background: repeating-linear-gradient(
      to bottom,
      var(--sky-blue) 0 48px,
      var(--sky-blue-light) 48px 96px
    );
    overflow: hidden;
  }
  .brand-square {
    position: absolute;
    left: 221px;
    top: 20px;
    width: 240px;
    height: 240px;
    background: var(--frame-violet);
  }
  .name-band {
    position: absolute;
    left: 0;
    right: 0;
    top: 270px;
    height: 236px;
    background: var(--sky-blue);
    border-top: 6px solid var(--frame-violet);
  }
  .name-plate {
    position: absolute;
    left: 20px;
    right: 20px;
    top: 60px;
    height: 140px;
    background: repeating-linear-gradient(
      to bottom,
      var(--band-white) 0 8px,
      var(--band-pale) 8px 16px
    );
    display: flex;
    align-items: center;
    justify-content: center;
  }
  .centre-name {
    font-family: "Poppins", sans-serif;
    font-weight: 700;
    font-size: 118px;
    line-height: 1;
    color: var(--frame-violet);
    letter-spacing: 1px;
    margin-top: 10px;
  }
  .leaf-motif {
    position: absolute;
    left: 52px;
    top: 540px;
    width: 580px;
    height: 600px;
  }
  .tagline {
    position: absolute;
    left: 0;
    right: 0;
    text-align: center;
    font-family: "Patrick Hand", cursive;
    color: var(--lettering-white);
    line-height: 1;
    margin: 0;
  }
  .tagline-shopping {
    top: 600px;
    font-size: 150px;
    letter-spacing: 2px;
  }
  .tagline-centre {
    top: 840px;
    font-size: 104px;
    letter-spacing: 2px;
  }
</style>
</head>
<body>
  <main class="sign">
    <div class="brand-square" aria-hidden="true"></div>

    <section class="name-band">
      <div class="name-plate">
        <h1 class="centre-name">Fernhill</h1>
      </div>
    </section>

    <svg class="leaf-motif" viewBox="0 0 580 600" role="img" aria-label="Curled green leaf illustration forming a swirl behind the lettering">
      <defs>
        <radialGradient id="leafTone" cx="45%" cy="45%" r="60%">
          <stop offset="0%" stop-color="var(--leaf-green-light)"/>
          <stop offset="100%" stop-color="var(--leaf-green)"/>
        </radialGradient>
      </defs>
      <ellipse cx="290" cy="300" rx="280" ry="290" fill="url(#leafTone)"/>
    </svg>

    <p class="tagline tagline-shopping">SHOPPING</p>
    <p class="tagline tagline-centre">CENTRE</p>
  </main>
</body>
</html>
```